Buch-/eBook-Cover für Geschichte zum Pride auf Gran Canaria
Zielgruppe
Zielgruppe: Reisefreudige junge schwule Männer
Aufgabenstellung
Die Geschichte spielt zum Pride auf Gran Canaria. Es geht um vier Freunde die dort ihre Ferien verbingen.
Ich stelle mir vor, dass auf dem Cover die Regenbogenflagge ist, Strand, Meer, keine Menschen und ein fetter Schriftzug mit dem Titel #TorvilenaGlanz. Daneben sollte kleiner mein Name Ferdinand zu Brakwede stehen. Das Cover kann aber auch gern wie ein Partyflyer designt sein und der Titel wie ein Logo wirken.
Bin aber für alternativen offen.

```html
<!DOCTYPE html>
<html lang="de">
<head>
<meta charset="utf-8">
<title>#TorvilenaGlanz – Ferdinand zu Brakwede</title>
<link rel="stylesheet" href="https://fonts.googleapis.com/css2?family=Titan+One&family=Montserrat:wght@600&display=swap">
<style>
  :root {
    --sky-top: #f5f8ec;
    --sky-mid: #f8f6ea;
    --sky-low: #cfe6ef;
    --horizon: #8fcbe4;
    --sea: #2eaed6;
    --sea-near: #6cc6e0;
    --sand-light: #e2d3b4;
    --sand: #d6c29f;
    --sand-dark: #a88d6c;
    --stripe-purple: #a3299a;
    --stripe-blue: #4a6cb3;
    --stripe-green: #139a42;
    --stripe-yellow: #ddcb21;
    --stripe-orange: #d99217;
    --stripe-red: #cf0b12;
    --title-ink: #000000;
    --author-ink: #ffffff;
  }
  * { margin: 0; padding: 0; box-sizing: border-box; }
  html, body { width: 752px; height: 1200px; overflow: hidden; background: #ffffff; }
  .cover {
    position: relative;
    width: 752px;
    height: 1200px;
    overflow: hidden;
  }
  .beach-scene {
    position: absolute;
    inset: 0;
    background: linear-gradient(to bottom,
      var(--sky-top) 0%,
      var(--sky-mid) 38%,
      var(--sky-low) 48%,
      var(--horizon) 53.6%,
      var(--sea) 53.8%,
      var(--sea-near) 58.2%,
      var(--sand-light) 58.6%,
      var(--sand) 80%,
      var(--sand-dark) 100%);
  }
  .rainbow-band {
    position: absolute;
    top: 0;
    left: 225px;
    width: 296px;
    height: 1200px;
    display: flex;
  }
  .rainbow-band span { flex: 1; }
  .rainbow-band .purple { background: var(--stripe-purple); }
  .rainbow-band .blue { background: var(--stripe-blue); }
  .rainbow-band .green { background: var(--stripe-green); }
  .rainbow-band .yellow { background: var(--stripe-yellow); }
  .rainbow-band .orange { background: var(--stripe-orange); }
  .rainbow-band .red { background: var(--stripe-red); }
  .title {
    position: absolute;
    top: 218px;
    left: 0;
    width: 752px;
    text-align: center;
    font-family: "Titan One", sans-serif;
    color: var(--title-ink);
    text-transform: uppercase;
    font-size: 86px;
    line-height: 90px;
    letter-spacing: 1px;
    font-weight: 400;
  }
  .title .line { display: block; }
  .author {
    position: absolute;
    top: 1082px;
    left: 0;
    width: 752px;
    text-align: center;
    font-family: "Montserrat", sans-serif;
    font-weight: 600;
    font-size: 37px;
    letter-spacing: 2.5px;
    color: var(--author-ink);
  }
</style>
</head>
<body>
  <main class="cover">
    <div class="beach-scene" role="img" aria-label="Foto: Sanddünen mit Sträuchern und einer Palme, dahinter das blaue Meer unter hellem, leicht bewölktem Himmel"></div>
    <div class="rainbow-band" aria-hidden="true">
      <span class="purple"></span>
      <span class="blue"></span>
      <span class="green"></span>
      <span class="yellow"></span>
      <span class="orange"></span>
      <span class="red"></span>
    </div>
    <h1 class="title">
      <span class="line">#Torvilena</span>
      <span class="line">Glanz</span>
    </h1>
    <p class="author">Ferdinand zu Brakwede</p>
  </main>
</body>
</html>
```